Single-sided business card for restaurant velmora with new logo made on this site

Business card options with new logo including restaurant name, address, phone number and website. This business card is single-sided only and will be presented at the hostess desk for clients to take. I would like to see options based on a cream card background, a white card background, a yellow card background and a burgundy colored background. It needs to be elegant and traditional.

Target Market(s)

local and international crowd

Industry/Entity Type

restaurant

Contact Information for Business Card

address, website and phone number

Font styles to use
Serif

Colors
EE7325
F08F49
F5BC92
FAE3D3
FDF4ED

Requirements
Must have
• new logo, address, phone number, website
Should not have
• more than three colors

```html
<!DOCTYPE html>
<html lang="es">
<head>
<meta charset="utf-8">
<title>Velmora – Tarjeta de presentación</title>
<link rel="stylesheet" href="https://fonts.googleapis.com/css2?family=Cinzel:wght@400&family=Raleway:wght@400&display=swap">
<style>
  :root {
    --backdrop: #1d1d1d;
    --card: #33191c;
    --ink: #f4ece6;
    --mark: #f2b233;
    --agave-light: #d0636b;
    --agave-mid: #7a3038;
    --agave-dark: #1a0c0d;
  }
  * { margin: 0; padding: 0; box-sizing: border-box; }
  html, body {
    width: 1200px;
    height: 800px;
    overflow: hidden;
    background: var(--backdrop);
  }
  .business-card {
    position: absolute;
    left: 75px;
    top: 100px;
    width: 1050px;
    height: 600px;
    background: var(--card);
    color: var(--ink);
    font-family: "Raleway", sans-serif;
    font-weight: 400;
    overflow: hidden;
  }
  .brand {
    position: absolute;
    left: 64px;
    top: 64px;
    width: 214px;
    display: flex;
    flex-direction: column;
    align-items: center;
    font-family: "Cinzel", serif;
    font-weight: 400;
  }
  .brand-square {
    width: 126px;
    height: 126px;
    background: var(--mark);
  }
  .brand-name {
    margin-top: 18px;
    font-size: 36px;
    line-height: 1;
    letter-spacing: 0.12em;
    margin-right: -0.12em;
    text-transform: uppercase;
    color: var(--ink);
  }
  .brand-since {
    margin-top: 10px;
    width: 100%;
    display: flex;
    align-items: center;
    gap: 10px;
    font-size: 10px;
    letter-spacing: 0.06em;
    text-transform: uppercase;
  }
  .brand-since::before,
  .brand-since::after {
    content: "";
    flex: 1;
    height: 1.5px;
    background: var(--ink);
  }
  .contact {
    position: absolute;
    left: 67px;
    top: 320px;
    font-size: 23px;
    line-height: 1.27;
    font-style: normal;
  }
  .contact p + p { margin-top: 12px; }
  .agave-artwork {
    position: absolute;
    left: 356px;
    top: 102px;
    width: 680px;
    height: 492px;
    border-radius: 50% 50% 4px 4px / 100% 100% 4px 4px;
    background: linear-gradient(100deg, var(--agave-light) 0%, var(--agave-mid) 38%, var(--agave-dark) 78%);
    opacity: 0.9;
  }
</style>
</head>
<body>
  <article class="business-card">
    <div class="brand">
      <div class="brand-square"></div>
      <div class="brand-name">Velmora</div>
      <div class="brand-since">Desde 1999</div>
    </div>

    <address class="contact">
      <p>Restaurant Velmora<br>Jacaranda 417<br>Bahías de Solcanto<br>Oaxaca CP 70412</p>
      <p>Reservaciones<br>958-555-0142</p>
      <p>www.velmora.com.mx</p>
    </address>

    <div class="agave-artwork" role="img" aria-label="Large agave plant illustration in rose-to-burgundy gradient"></div>
  </article>
</body>
</html>
```